Probate (Legal) Wordpress Design with Coding for Online Company

I need a Wordpress design with coding, pictures, content to be provided by me, fully responsive, and development. This is for a 6-7 page design.

Pages Needed: Home/About/Probate/Process/FAQ/Contact Us/Blog.

The home page should be organized as followed:
-Steps in Probate: Gather; Implement; Close (each step will come with content)
-Flat-Fee Price & Savings: Content will go here with a button to contact us (phone number) or just the phone number.
-You Have Questions, We Have Answers: five questions with content. Only one question answer to show at a time when clicked on the question from the list.
-Get to Know Us: a brief description with content about what we do and who we are.

Main image slogan: Helping Californians deal with loss with DIGNITY & UNDERSTATING (you may use a better slogan if you wish).

The Contact page should not have a map since we are an online company. We service the entire state of California in every county and city.

The About page should be simple, direct, and easy on the eye. It should have a brief description of who we are and it should have no more than 6 reasons why the client should hire us.

About our online California company. We are not attorneys but legal document assistants who prepare legal documents for probate estate when someone dies with or without a will and assets need to be distributed. We have a flat-fee for Formal Probate of $999 and $699 for Informal Probate. We are an online company and offer our services to the entire state of California in every county. We do everything over the phone and email. The turn around time for us to prepare the initial legal paperwork for the client is within 3-5 business days. We can prepare, file, serve and manage a probate matter from petition to closing. We are not attorneys so our prices are very affordable compare to the attorney.

The company name for the website will be www.velmarhollow.com, The Velmar Hollow Group.

I do not have a logo yet. The colors of the website should be easy on the eye and calming. THE SITE SHOULD BE SIMPLE AND STRAIGHT TO THE POINT. EASY TO NAVIGATE.

The company phone number should be very visible and should stand out to the client. It should also be clickable and ready to dial for smartphone users.

I do not want a contact form on the homepage. THE MAIN THING IS FOR THE POTENTIAL CLIENT TO CALL OUR OFFICE TO SIGN UP.

I do like some images of family or people since we are dealing with people who just lost a loved one. Not all the images have to be of people.

The site should not look like we practice law or that people can mistake us for attorneys.

Target Market(s)

People who just lost a loved one who had property, assets, in California but died with or without a will or trust. This is for people looking to hire non-attorneys.

Coding

Coded - Design and coding required

Font styles to use
Serif

Colors

Designer to choose colors to be used in the design.

Requirements
Must have
• Refer to Project Description.
Nice to have
• The sample images provided is what I am attracted to for the homepage image.
Should not have

```html
<!DOCTYPE html>
<html lang="en">
<head>
<meta charset="utf-8">
<title>The Velmar Hollow Group — Probate Document Assistance</title>
<link href="https://fonts.googleapis.com/css2?family=Raleway:wght@400;600;700;800&family=Open+Sans:wght@400;600&display=swap" rel="stylesheet">
<style>
:root{
  --orange:#f7941d;
  --orange-dark:#e5801a;
  --blue:#2a8fd4;
  --ink:#2b2b2b;
  --body:#777;
  --line:#e3e3e3;
  --soft:#f5f7f9;
  --footer:#1f1f1f;
  --footer-bar:#161616;
  --white:#fff;
}
*{box-sizing:border-box;margin:0;padding:0}
html,body{width:1200px;height:3312px;overflow:hidden}
body{font-family:"Open Sans",sans-serif;color:var(--body);background:var(--white);font-size:13px;line-height:1.7}
.wrap{width:1000px;margin:0 auto;position:relative}
h1,h2,h3,h4{font-family:"Raleway",sans-serif;color:var(--ink)}

/* header */
.site-header{height:96px;background:var(--white)}
.site-header .wrap{height:96px}
.brand{position:absolute;left:0;top:20px;font-family:"Raleway",sans-serif;font-weight:800;font-size:27px;color:var(--ink);letter-spacing:1px}
.contact-strip{position:absolute;right:0;top:18px;display:flex;gap:30px;font-size:12px;color:var(--ink)}
.contact-strip span{display:flex;align-items:center;gap:7px}
.contact-strip b{font-weight:600}
.contact-strip .hl{color:var(--orange);font-weight:600}
.main-nav{position:absolute;right:0;top:52px;display:flex;align-items:center;gap:4px}
.main-nav a{font-family:"Raleway",sans-serif;font-weight:700;font-size:12.5px;color:var(--ink);text-decoration:none;padding:9px 13px}
.main-nav a.active{background:var(--orange);color:var(--white)}
.main-nav svg{margin-left:12px}

/* hero */
.hero{position:relative;height:392px;overflow:hidden}
.hero-photo{position:absolute;inset:0;background:linear-gradient(180deg,#b9d4e6 0%,#cfdcc2 45%,#8fae62 78%,#6f8f3f 100%)}
.hero-photo::after{content:"";position:absolute;inset:0;background:rgba(20,30,20,.18)}
.hero-copy{position:relative;text-align:center;padding-top:100px;color:var(--white)}
.hero-copy p{font-family:"Raleway",sans-serif;font-weight:600;font-size:34px;color:var(--white)}
.hero-copy h1{font-size:58px;font-weight:800;color:var(--white);letter-spacing:1px;margin-top:4px}
.hero-dots{position:absolute;bottom:20px;left:50%;transform:translateX(-50%);display:flex;gap:8px}
.hero-dots i{width:9px;height:9px;border-radius:50%;background:rgba(255,255,255,.55)}
.hero-dots i.on{background:var(--white)}

/* section heads */
.section-title{text-align:center;font-size:27px;font-weight:800;text-transform:uppercase;letter-spacing:.5px}
.section-rule{width:46px;height:2px;background:var(--orange);margin:14px auto 0}
.section-lead{text-align:center;width:640px;margin:18px auto 0;font-size:12.5px}

/* steps */
.steps{height:680px;padding-top:88px;border-bottom:1px solid var(--line)}
.step-cards{display:flex;justify-content:space-between;margin-top:94px}
.step-card{width:310px;height:300px;border:1px solid var(--line);text-align:center;padding:30px 28px 0}
.step-card h3{font-size:22px;font-weight:800;margin-top:14px;text-transform:uppercase}
.step-card p{font-size:12.5px;margin-top:12px}
.read-more{display:inline-block;margin-top:14px;font-family:"Raleway",sans-serif;font-weight:700;font-size:11px;color:var(--orange);text-transform:uppercase}

/* flat fee */
.flat-fee{position:relative;height:328px;overflow:hidden;text-align:center}
.flat-fee-photo{position:absolute;inset:0;background:linear-gradient(180deg,#3ea3e0 0%,#2a8fd4 55%,#3a9bdb 100%)}
.flat-fee .wrap{padding-top:54px}
.flat-fee h2{color:var(--white);font-size:30px;font-weight:700;text-transform:uppercase}
.flat-fee p{color:rgba(255,255,255,.92);width:620px;margin:14px auto 0;font-size:12.5px}
.btn{display:inline-block;background:var(--orange);color:var(--white);font-family:"Raleway",sans-serif;font-weight:700;font-size:13px;padding:14px 36px;border-radius:30px;text-transform:uppercase;margin-top:28px;text-decoration:none}

/* about */
.about{height:892px;padding-top:64px}
.about-row{display:flex;justify-content:space-between;align-items:flex-start}
.about-row.first{margin-top:54px}
.about-row.second{margin-top:32px}
.about-photo{width:508px;height:296px}
.photo-desk{background:linear-gradient(135deg,#c9d7e4 0%,#9eb4c8 50%,#e8ecef 100%)}
.photo-pen{width:500px;height:352px;background:linear-gradient(135deg,#d9dde0 0%,#aab3bb 55%,#f0f1f2 100%)}
.about-text{width:428px;padding-top:18px}
.about-text.left{width:470px;padding-top:24px}
.about-text h3{display:flex;align-items:center;gap:12px;font-size:24px;font-weight:800;text-transform:uppercase}
.about-text p{font-size:12.5px;margin-top:16px}
.btn-outline{display:inline-block;margin-top:22px;border:1px solid #cfcfcf;border-radius:20px;padding:7px 22px;font-family:"Raleway",sans-serif;font-weight:700;font-size:11px;color:var(--orange);text-transform:uppercase}

/* faq */
.faq{height:580px;background:var(--soft);padding-top:80px}
.faq-list{margin-top:36px}
.faq-item{border:1px solid #d6d9dc;background:var(--white);height:48px;display:flex;align-items:center;margin-bottom:18px;font-size:13px;color:var(--ink)}
.faq-item .mark{width:52px;text-align:center;font-weight:700;font-size:18px;color:var(--blue)}
.faq-item.open{background:var(--orange);border-color:var(--orange);color:var(--white);margin-bottom:0}
.faq-item.open .mark{color:var(--white)}
.faq-answer{border:1px solid #d6d9dc;border-top:none;background:var(--white);padding:22px 52px;font-size:12.5px;margin-bottom:18px;height:82px}

/* footer */
.site-footer{height:352px;background:var(--footer);color:#bdbdbd;position:relative}
.site-footer .wrap{padding-top:72px;display:flex}
.footer-brand{width:340px;padding-top:46px}
.footer-brand .brand-name{font-family:"Raleway",sans-serif;font-weight:800;font-size:29px;color:var(--white);letter-spacing:.5px;line-height:1;white-space:nowrap}
.footer-brand .phone{color:var(--white);font-weight:600;font-size:18px;margin-top:10px}
.footer-col h4{color:var(--white);font-size:14px;font-weight:700;text-transform:uppercase;margin-bottom:16px}
.footer-col ul{list-style:none;font-size:12px;line-height:2}
.col-links{width:222px}
.col-contact{width:300px}
.col-contact li{display:flex;gap:12px;align-items:flex-start;margin-bottom:6px;line-height:1.7}
.col-social li{display:flex;gap:14px;align-items:center;margin-bottom:12px}
.col-social .sq{width:22px;height:22px;background:#555;flex:none}
.footer-bar{position:absolute;left:0;right:0;bottom:0;height:40px;background:var(--footer-bar);text-align:center;font-size:11.5px;line-height:40px;color:#9a9a9a}
.to-top{position:absolute;right:30px;bottom:8px;width:24px;height:24px;background:#333}
</style>
</head>
<body>

<header class="site-header">
  <div class="wrap">
    <div class="brand">VELMAR HOLLOW</div>
    <div class="contact-strip">
      <span>
        <svg width="14" height="14" viewBox="0 0 24 24"><path fill="#f7941d" d="M6.6 10.8a15 15 0 0 0 6.6 6.6l2.2-2.2a1 1 0 0 1 1-.25 11.4 11.4 0 0 0 3.6.57 1 1 0 0 1 1 1V20a1 1 0 0 1-1 1A17 17 0 0 1 3 4a1 1 0 0 1 1-1h3.5a1 1 0 0 1 1 1c0 1.25.2 2.45.57 3.6a1 1 0 0 1-.25 1z"/></svg>
        <b>CALL US NOW:</b> <span class="hl">1 800 555 0142</span>
      </span>
      <span>
        <svg width="14" height="14" viewBox="0 0 24 24"><rect x="2" y="5" width="20" height="14" rx="2" fill="#f7941d"/><path d="M3 6l9 7 9-7" stroke="#fff" stroke-width="1.8" fill="none"/></svg>
        <b>EMAIL US:</b> <span class="hl">info@velmarhollow.com</span>
      </span>
    </div>
    <nav class="main-nav">
      <a class="active" href="#">HOME</a>
      <a href="#">ABOUT</a>
      <a href="#">PROBATE</a>
      <a href="#">PROCESS</a>
      <a href="#">FAQ</a>
      <a href="#">CONTACT US</a>
      <a href="#">BLOG</a>
      <svg width="15" height="15" viewBox="0 0 24 24"><circle cx="10" cy="10" r="7" stroke="#2b2b2b" stroke-width="2.5" fill="none"/><path d="M15 15l6 6" stroke="#2b2b2b" stroke-width="2.5"/></svg>
    </nav>
  </div>
</header>

<section class="hero">
  <div class="hero-photo" role="img" aria-label="Photo of a family relaxing together on a sunny lawn"></div>
  <div class="hero-copy">
    <p>Helping Californians deal with loss with</p>
    <h1>DIGNITY &amp; UNDERSTATING</h1>
  </div>
  <div class="hero-dots"><i></i><i class="on"></i><i></i></div>
</section>

<section class="steps">
  <div class="wrap">
    <h2 class="section-title">Steps in Probate</h2>
    <div class="section-rule"></div>
    <p class="section-lead">We are not attorneys but legal document assistants who prepare legal documents for probate estates when someone dies with or without a will and assets need to be distributed.</p>
    <div class="step-cards">
      <div class="step-card">
        <svg width="40" height="34" viewBox="0 0 40 34"><circle cx="20" cy="8" r="6" fill="#2a8fd4"/><circle cx="8" cy="12" r="4.5" fill="#2a8fd4"/><circle cx="32" cy="12" r="4.5" fill="#2a8fd4"/><path d="M10 32c0-8 4-13 10-13s10 5 10 13z" fill="#2a8fd4"/><path d="M0 30c0-6 3-10 8-10 2 0 3 .5 4 1-2 2-3 5-3 9z" fill="#2a8fd4"/><path d="M40 30c0-6-3-10-8-10-2 0-3 .5-4 1 2 2 3 5 3 9z" fill="#2a8fd4"/></svg>
        <h3>Gather</h3>
        <p>We can prepare, file, serve and manage a probate matter from petition to closing. We gather every record needed with you over phone and email.</p>
        <span class="read-more">Read more</span>
      </div>
      <div class="step-card">
        <svg width="40" height="36" viewBox="0 0 40 36"><circle cx="14" cy="20" r="9" fill="none" stroke="#2a8fd4" stroke-width="5" stroke-dasharray="4 3"/><circle cx="14" cy="20" r="4" fill="#2a8fd4"/><circle cx="31" cy="8" r="6" fill="none" stroke="#2a8fd4" stroke-width="4" stroke-dasharray="3 2"/><circle cx="31" cy="8" r="2.5" fill="#2a8fd4"/></svg>
        <h3>Implement</h3>
        <p>We can prepare, file, serve and manage a probate matter from petition to closing. Initial paperwork is ready within 3-5 business days.</p>
        <span class="read-more">Read more</span>
      </div>
      <div class="step-card">
        <svg width="36" height="36" viewBox="0 0 36 36"><circle cx="18" cy="18" r="15" fill="none" stroke="#2a8fd4" stroke-width="4"/><path d="M12 12l12 12M24 12L12 24" stroke="#2a8fd4" stroke-width="4"/></svg>
        <h3>Close</h3>
        <p>We can prepare, file, serve and manage a probate matter from petition to closing. We see the estate through until it is closed.</p>
        <span class="read-more">Read more</span>
      </div>
    </div>
  </div>
</section>

<section class="flat-fee">
  <div class="flat-fee-photo" role="img" aria-label="City skyline photo tinted in blue"></div>
  <div class="wrap">
    <h2>Flat-Fee Price &amp; Savings</h2>
    <p>Our flat fee is $999 for Formal Probate and $699 for Informal Probate across every California county. We can prepare, file, serve and manage a probate matter from petition to closing.</p>
    <a class="btn" href="tel:18005550142">Contact Us</a>
  </div>
</section>

<section class="about">
  <div class="wrap">
    <h2 class="section-title">Get to Know Us</h2>
    <div class="section-rule"></div>
    <div class="about-row first">
      <div class="about-photo photo-desk" role="img" aria-label="Photo of an estate planning folder on a desk beside a family picture"></div>
      <div class="about-text">
        <h3>
          <svg width="30" height="26" viewBox="0 0 40 34"><circle cx="20" cy="8" r="6" fill="#2a8fd4"/><circle cx="8" cy="12" r="4.5" fill="#2a8fd4"/><circle cx="32" cy="12" r="4.5" fill="#2a8fd4"/><path d="M10 32c0-8 4-13 10-13s10 5 10 13z" fill="#2a8fd4"/><path d="M0 30c0-6 3-10 8-10 2 0 3 .5 4 1-2 2-3 5-3 9z" fill="#2a8fd4"/><path d="M40 30c0-6-3-10-8-10-2 0-3 .5-4 1 2 2 3 5 3 9z" fill="#2a8fd4"/></svg>
          Who We Are
        </h3>
        <p>We are not attorneys but legal document assistants who prepare legal documents for probate estates when someone dies with or without a will and assets need to be distributed. We have a flat fee of $999 for Formal Probate and $699 for Informal Probate. We are an online company and offer our services statewide.</p>
        <span class="btn-outline">Read more</span>
      </div>
    </div>
    <div class="about-row second">
      <div class="about-text left">
        <h3>
          <svg width="30" height="27" viewBox="0 0 40 36"><circle cx="14" cy="20" r="9" fill="none" stroke="#2a8fd4" stroke-width="5" stroke-dasharray="4 3"/><circle cx="14" cy="20" r="4" fill="#2a8fd4"/><circle cx="31" cy="8" r="6" fill="none" stroke="#2a8fd4" stroke-width="4" stroke-dasharray="3 2"/><circle cx="31" cy="8" r="2.5" fill="#2a8fd4"/></svg>
          What We Do
        </h3>
        <p>We are not attorneys but legal document assistants who prepare legal documents for probate estates when someone dies with or without a will and assets need to be distributed. We have a flat fee of $999 for Formal Probate and $699 for Informal Probate. We are an online company and offer our services statewide.</p>
        <span class="btn-outline">Read more</span>
      </div>
      <div class="photo-pen" role="img" aria-label="Photo of a hand signing documents next to a laptop"></div>
    </div>
  </div>
</section>

<section class="faq">
  <div class="wrap">
    <h2 class="section-title">FAQs</h2>
    <div class="section-rule"></div>
    <div class="faq-list">
      <div class="faq-item open"><span class="mark">−</span>At vero eos et accusamus et iusto odio dignissimos ducimus qui blanditiis?</div>
      <div class="faq-answer">Nam libero tempore, cum soluta nobis est eligendi optio cumque nihil impedit quo minus id quod maxime placeat facere possimus.</div>
      <div class="faq-item"><span class="mark">+</span>At vero eos et accusamus et iusto odio dignissimos ducimus qui blanditiis?</div>
      <div class="faq-item"><span class="mark">+</span>At vero eos et accusamus et iusto odio dignissimos ducimus qui blanditiis?</div>
      <div class="faq-item"><span class="mark">+</span>At vero eos et accusamus et iusto odio dignissimos ducimus qui blanditiis?</div>
      <div class="faq-item"><span class="mark">+</span>At vero eos et accusamus et iusto odio dignissimos ducimus qui blanditiis?</div>
    </div>
  </div>
</section>

<footer class="site-footer">
  <div class="wrap">
    <div class="footer-brand">
      <div class="brand-name">VELMAR HOLLOW</div>
      <div class="phone">1 800 555 0142</div>
    </div>
    <div class="footer-col col-links">
      <h4>Quick Links</h4>
      <ul><li>Home</li><li>FAQ</li><li>Support</li><li>Sitemap</li><li>Terms Of Use</li><li>Privacy Statement</li></ul>
    </div>
    <div class="footer-col col-contact">
      <h4>Contact Us</h4>
      <ul>
        <li><svg width="12" height="16" viewBox="0 0 12 16"><path d="M6 0a6 6 0 0 1 6 6c0 4-6 10-6 10S0 10 0 6a6 6 0 0 1 6-6z" fill="#bdbdbd"/><circle cx="6" cy="6" r="2.2" fill="#1f1f1f"/></svg><span>Suite 14, 220 Alder Row<br>Fernbrook, CA 95821</span></li>
        <li><svg width="12" height="12" viewBox="0 0 24 24"><path fill="#bdbdbd" d="M6.6 10.8a15 15 0 0 0 6.6 6.6l2.2-2.2a1 1 0 0 1 1-.25 11.4 11.4 0 0 0 3.6.57 1 1 0 0 1 1 1V20a1 1 0 0 1-1 1A17 17 0 0 1 3 4a1 1 0 0 1 1-1h3.5a1 1 0 0 1 1 1c0 1.25.2 2.45.57 3.6a1 1 0 0 1-.25 1z"/></svg><span>1 800 555 0142</span></li>
        <li><svg width="12" height="12" viewBox="0 0 24 24"><rect x="2" y="5" width="20" height="14" rx="2" fill="#bdbdbd"/><path d="M3 6l9 7 9-7" stroke="#1f1f1f" stroke-width="2" fill="none"/></svg><span>info@velmarhollow.com</span></li>
      </ul>
    </div>
    <div class="footer-col col-social">
      <h4>Social Media</h4>
      <ul>
        <li><span class="sq"></span>Community</li>
        <li><span class="sq"></span>Updates</li>
        <li><span class="sq"></span>Network</li>
      </ul>
    </div>
  </div>
  <div class="footer-bar">Copyright © 2017, The Velmar Hollow Group. All rights reserved.</div>
  <div class="to-top"></div>
</footer>

</body>
</html>
```